Weightloss company needs Business Card

We want a business card that is clean and professional, yet portrays that we are a friendly, innovative, and versatile program designed to fit the needs of our clients.
I would like there to be 2 sides, one side having an appointment card, and the other side containing the logo and business information. There can be decorations on both sides. The logo is attached.

Target Market(s)

Men and women 40-60

Industry/Entity Type

Business

Contact Information for Business Card

Font styles to use
Sans Serif

Requirements
Must have
• The logo, space for business information
Nice to have
• The colors in the logo
Should not have
• No pictures of people or food

```html
<!DOCTYPE html>
<html lang="en">
<head>
<meta charset="utf-8">
<title>Brightpath Weightloss – Business Card</title>
<link rel="stylesheet" href="https://fonts.googleapis.com/css2?family=Source+Sans+3:ital,wght@0,400;0,600;0,700;1,400&display=swap">
<style>
  :root {
    --backdrop: #3b3b3b;
    --card-white: #ffffff;
    --card-tint: #d8f6fc;
    --brand-red: #ff0033;
    --brand-cyan: #22d8f5;
    --text-grey: #555555;
    --rule-grey: #6d6d6d;
  }
  * { box-sizing: border-box; margin: 0; padding: 0; }
  html, body {
    width: 1105px; height: 1200px; overflow: hidden;
    background: var(--backdrop);
    font-family: "Source Sans 3", sans-serif;
  }
  .card {
    position: absolute; left: 196px; width: 720px; height: 413px;
    border-radius: 19px; overflow: hidden;
  }
  .card--front { top: 145px; background: var(--card-white); }
  .card--back { top: 602px; background: var(--card-tint); }

  .swoosh { position: absolute; inset: 0; width: 720px; height: 413px; }

  .brand {
    position: absolute; display: flex; align-items: center; gap: 10px;
    color: var(--brand-red); font-weight: 700; line-height: 1;
  }
  .brand__mark {
    width: 16px; height: 16px; border-radius: 50%;
    background: var(--brand-red); flex: none;
  }
  .card--front .brand { left: 39px; top: 58px; font-size: 31px; }
  .card--back .brand { right: 50px; top: 62px; font-size: 26px; }

  .address {
    position: absolute; left: 39px; top: 176px;
    color: var(--text-grey); font-size: 19px; line-height: 27px;
  }
  .contact-list {
    position: absolute; left: 39px; top: 235px; list-style: none;
    color: var(--text-grey); font-size: 19px;
  }
  .contact-list li { display: flex; align-items: center; height: 27.7px; }
  .contact-list svg { width: 18px; height: 18px; margin-right: 12px; fill: var(--brand-red); }

  .person {
    position: absolute; right: 44px; top: 312px; text-align: right;
    color: #fff; text-transform: uppercase;
  }
  .person__name { font-size: 25px; font-weight: 600; letter-spacing: 0.5px; line-height: 1.1; }
  .person__title { font-size: 19px; line-height: 1.3; }

  .appointment__heading {
    position: absolute; left: 48px; top: 52px;
    color: var(--brand-red); font-size: 27px; font-weight: 700;
  }
  .appointment__row {
    position: absolute; left: 54px; width: 620px; height: 30px;
    color: var(--text-grey); font-size: 20px;
  }
  .appointment__row span { position: absolute; bottom: 2px; }
  .appointment__row .field-line {
    position: absolute; bottom: 6px; height: 1.5px; background: var(--rule-grey);
  }
  .label-date { left: 0; }
  .line-date { left: 62px; width: 255px; }
  .label-time { left: 334px; }
  .line-time { left: 393px; width: 142px; }
  .label-ampm { left: 550px; }

  .appointment__notice {
    position: absolute; left: 0; right: 0; top: 356px; text-align: center;
    color: var(--text-grey); font-size: 17px; font-style: italic;
  }
</style>
</head>
<body>

<section class="card card--front" aria-label="Card front">
  <svg class="swoosh" viewBox="0 0 720 413" aria-hidden="true">
    <path d="M220,413 C450,320 570,200 640,0 L720,0 L720,6 C650,230 460,330 234,413 Z" fill="var(--brand-cyan)"/>
    <path d="M234,413 C460,330 650,230 720,6 L720,413 Z" fill="var(--brand-red)"/>
    <path d="M234,413 C460,330 650,230 720,6" fill="none" stroke="#fff" stroke-width="3"/>
  </svg>

  <div class="brand"><span>Brightpath Weightloss</span><span class="brand__mark"></span></div>

  <p class="address">4120 Willow Crest Drive<br>Juneau, Alaska 99801</p>

  <ul class="contact-list">
    <li><svg viewBox="0 0 24 24"><path d="M6.6 10.8a15.1 15.1 0 0 0 6.6 6.6l2.2-2.2a1 1 0 0 1 1-.25 11.4 11.4 0 0 0 3.6.57 1 1 0 0 1 1 1V20a1 1 0 0 1-1 1A17 17 0 0 1 3 4a1 1 0 0 1 1-1h3.5a1 1 0 0 1 1 1c0 1.25.2 2.45.57 3.57a1 1 0 0 1-.25 1z"/></svg>555 214 7730</li>
    <li><svg viewBox="0 0 24 24"><path d="M7 1h10a2 2 0 0 1 2 2v18a2 2 0 0 1-2 2H7a2 2 0 0 1-2-2V3a2 2 0 0 1 2-2zm0 3v14h10V4zm5 15.5a1.2 1.2 0 1 0 0 2.4 1.2 1.2 0 0 0 0-2.4z"/></svg>555 390 1186</li>
    <li><svg viewBox="0 0 24 24"><path d="M6 2h12v5H6zM3 8h18a2 2 0 0 1 2 2v7h-4v5H5v-5H1v-7a2 2 0 0 1 2-2zm4 8v4h10v-4z"/></svg>555 472 6051</li>
    <li><svg viewBox="0 0 24 24"><path d="M2 5h20v14H2zm2 2v.5l8 5 8-5V7z"/></svg>hello@brightpathwl.com</li>
    <li><svg viewBox="0 0 24 24"><path d="M12 2a10 10 0 1 0 0 20 10 10 0 0 0 0-20zm-1 17.9A8 8 0 0 1 4.2 10L9 14.8v1a2 2 0 0 0 2 2zm6.9-2.5a2 2 0 0 0-1.9-1.4h-1v-3a1 1 0 0 0-1-1H8v-2h2a1 1 0 0 0 1-1V7h2a2 2 0 0 0 2-2v-.4a8 8 0 0 1 2.9 12.8z"/></svg>www.brightpathwl.com</li>
  </ul>

  <div class="person">
    <p class="person__name">Daniel Hart</p>
    <p class="person__title">CEO/Founder</p>
  </div>
</section>

<section class="card card--back" aria-label="Appointment card">
  <h2 class="appointment__heading">Next Appointment</h2>
  <div class="brand"><span>Brightpath Weightloss</span><span class="brand__mark"></span></div>

  <div class="appointment__row" style="top:160px">
    <span class="label-date">Date</span><i class="field-line line-date"></i>
    <span class="label-time">Time</span><i class="field-line line-time"></i>
    <span class="label-ampm">am/pm</span>
  </div>
  <div class="appointment__row" style="top:233px">
    <span class="label-date">Date</span><i class="field-line line-date"></i>
    <span class="label-time">Time</span><i class="field-line line-time"></i>
    <span class="label-ampm">am/pm</span>
  </div>
  <div class="appointment__row" style="top:298px">
    <span class="label-date">Date</span><i class="field-line line-date"></i>
    <span class="label-time">Time</span><i class="field-line line-time"></i>
    <span class="label-ampm">am/pm</span>
  </div>

  <p class="appointment__notice">Please give 24 hours notice cancelling your appointment or a fee may be charged</p>
</section>

</body>
</html>
```